Stationery & Envelope Design

Executive Style looking stationery & envelope design.
Business Information:
Halden Crest Homes
418 Marlow Avenue, Fairbrook, OR 97402-1135
Phone: 541.555.0142
Fax: 541.555.0187

Industry/Entity Type

Business

```html
<!DOCTYPE html>
<html lang="en">
<head>
<meta charset="utf-8">
<title>Halden Crest Homes — Stationery Set</title>
<link href="https://fonts.googleapis.com/css2?family=Arimo:wght@400;700&display=swap" rel="stylesheet">
<style>
:root{
  --navy:#1f3f86;
  --blue:#0b55a0;
  --green:#7a8b36;
  --paper:#ffffff;
  --ink:#222222;
  --stage:#e9e4dc;
  --edge:#b9b9b9;
  --faint:#e6e8f1;
}
*{margin:0;padding:0;box-sizing:border-box}
html,body{width:1200px;height:1097px;overflow:hidden}
body{background:var(--stage);font-family:"Arimo",Arial,sans-serif;position:relative;color:var(--ink)}
.sheet,.envelope{position:absolute;background:var(--paper);border:1px solid var(--edge);overflow:hidden}
.sheet{width:474px;height:615px;top:38px}
.fax-sheet{left:86px}
.letterhead{left:585px}
.brand-name{position:absolute;font-weight:700;text-transform:uppercase;color:var(--navy);white-space:nowrap;letter-spacing:.5px}
.fax-sheet .brand-name{left:25px;top:58px;font-size:15px}
.fax-title{position:absolute;left:25px;top:128px;font-size:29px;font-weight:400}
.fax-field{position:absolute;font-size:11px;border-bottom:1.5px solid #333;padding-bottom:9px}
.fax-field.left{left:30px;width:246px}
.fax-field.right{left:285px;width:140px}
.footer-rule{position:absolute;left:0;width:100%;height:3px;background:var(--green)}
.footer-band{position:absolute;left:0;bottom:0;width:100%;background:var(--blue)}
.sheet .footer-rule{bottom:86px}
.sheet .footer-band{height:80px}
.band-text{position:absolute;color:#fff;font-size:9px;letter-spacing:.4px}
.fax-contacts{left:12px;bottom:12px;line-height:14px}
.fax-address{right:14px;bottom:14px;text-align:right;font-weight:700;line-height:14px}
.fax-address .firm{font-size:11px;display:block;margin-bottom:3px}
.letterhead .brand-name{left:0;width:100%;text-align:center;top:56px;font-size:14px}
.lh-contacts{position:absolute;left:371px;top:32px;font-size:9px;color:var(--navy);line-height:13px;border-left:1px solid #ccc;padding-left:4px}
.lh-watermark{position:absolute;left:0;width:100%;top:320px;text-align:center;font-weight:700;font-size:34px;color:var(--faint);text-transform:uppercase;letter-spacing:1px}
.lh-footer{left:0;width:100%;text-align:center;bottom:16px;font-weight:700}
.envelope{width:531px;height:230px}
.env-back-a{left:79px;top:678px}
.env-back-b{left:53px;top:749px}
.env-front{left:36px;top:825px;border-color:#555}
.env-front .brand-name{left:15px;top:45px;font-size:11px}
.env-front .footer-band{height:62px}
.env-front .footer-rule{bottom:68px}
.env-front .band-text{left:16px;bottom:14px;font-weight:700}
.flap{position:absolute;left:0;top:0;width:100%;height:72px}
.flap-name{position:absolute;left:0;width:100%;text-align:center;top:26px;font-weight:700;font-size:12px;text-transform:uppercase;letter-spacing:.5px}
.env-right-a{left:627px;top:669px;height:300px}
.env-right-b{left:611px;top:740px}
.env-right-c{left:645px;top:821px}
</style>
</head>
<body>

<section class="sheet fax-sheet">
  <div class="brand-name">Halden Crest Homes</div>
  <h1 class="fax-title">FAX</h1>
  <div class="fax-field left" style="top:196px">To</div>
  <div class="fax-field right" style="top:196px">From</div>
  <div class="fax-field left" style="top:254px">Fax</div>
  <div class="fax-field right" style="top:254px">Pages</div>
  <div class="fax-field left" style="top:308px">Phone</div>
  <div class="fax-field right" style="top:308px">Date</div>
  <div class="fax-field left" style="top:365px">Re</div>
  <div class="fax-field right" style="top:365px">CC</div>
  <div class="footer-rule"></div>
  <div class="footer-band"></div>
  <div class="band-text fax-contacts">&#9990; 541.555.0142<br>&#9990; 541.555.0187</div>
  <div class="band-text fax-address"><span class="firm">Halden Crest Homes</span>418 Marlow Avenue<br>Fairbrook, OR 97402-1135</div>
</section>

<section class="sheet letterhead">
  <div class="brand-name">Halden Crest Homes</div>
  <div class="lh-contacts">&#9990; 541.555.0142<br>&#9990; 541.555.0187</div>
  <div class="lh-watermark">Halden Crest Homes</div>
  <div class="footer-rule"></div>
  <div class="footer-band"></div>
  <div class="band-text lh-footer">Halden Crest Homes, 418 Marlow Avenue, Fairbrook, OR 97402-1135</div>
</section>

<section class="envelope env-back-a">
  <svg class="flap" viewBox="0 0 531 72" preserveAspectRatio="none"><path d="M0,0 L531,0 L515,72 L16,72Z" fill="#fff" stroke="var(--edge)"/></svg>
  <div class="flap-name" style="color:var(--navy)">Halden Crest Homes</div>
</section>

<section class="envelope env-back-b">
  <svg class="flap" viewBox="0 0 531 72" preserveAspectRatio="none"><path d="M0,0 L531,0 L515,72 L16,72Z" fill="#fff" stroke="var(--edge)"/></svg>
  <div class="flap-name" style="color:#555">Halden Crest Homes</div>
</section>

<section class="envelope env-front">
  <div class="brand-name">Halden Crest Homes</div>
  <div class="footer-rule"></div>
  <div class="footer-band"></div>
  <div class="band-text">Halden Crest Homes, 418 Marlow Avenue, Fairbrook, OR 97402-1135</div>
</section>

<section class="envelope env-right-a">
  <svg class="flap" viewBox="0 0 531 72" preserveAspectRatio="none"><path d="M0,0 L531,0 L515,72 L16,72Z" fill="var(--green)"/></svg>
  <div class="flap-name" style="color:#fff">Halden Crest Homes</div>
</section>

<section class="envelope env-right-b">
  <svg class="flap" viewBox="0 0 531 72" preserveAspectRatio="none"><path d="M0,0 L531,0 L515,72 L16,72Z" fill="var(--blue)"/></svg>
  <div class="flap-name" style="color:#fff">Halden Crest Homes</div>
</section>

<section class="envelope env-right-c">
  <svg class="flap" viewBox="0 0 531 72" preserveAspectRatio="none"><path d="M0,0 L531,0 L515,72 L16,72Z" fill="#fff" stroke="var(--edge)"/></svg>
  <div class="flap-name" style="color:#111">Halden Crest Homes</div>
</section>

</body>
</html>
```